Personal training and nutrition business needs business card design

We need a business card that outlays our services and invites potential customers to join our team and take the first step to a healthier and more enjoyable life. We cater for any level of fitness and specialize in weight loss and conditioning, strength training, muscle gain and strength endurance. Whether you are just starting off or need some help getting to the next level of your journey we are here to get the job done.
We specialize in one on one or one on two personal training sessions and each program will be custom made to suit individual fitness goals of our clients

```html
<!DOCTYPE html>
<html lang="en">
<head>
<meta charset="utf-8">
<title>Pulse &amp; Pace — Business Card</title>
<link rel="stylesheet" href="https://fonts.googleapis.com/css2?family=Exo+2:ital,wght@0,700;1,700&family=Oswald:wght@500&family=Roboto:wght@400&display=swap">
<style>
  :root {
    --backdrop: #2a2a2a;
    --card-black: #1b1b1d;
    --front-black: #1d1d1f;
    --purple-deep: #5a3a8e;
    --purple-mid: #7a4596;
    --purple-light: #9b55a8;
    --edge-purple: #a35fb8;
    --tag-purple: #a05bb0;
    --emboss-grey: #3b3b3e;
    --white: #f4f2f6;
  }
  * { margin: 0; padding: 0; box-sizing: border-box; }
  html, body { width: 1200px; height: 1138px; overflow: hidden; }
  body { background: var(--backdrop); position: relative; }

  .card {
    position: absolute;
    width: 620px;
    height: 374px;
    border-radius: 13px;
    overflow: hidden;
  }

  /* Front side */
  .card-front { left: 274px; top: 186px; background: var(--front-black); }
  .front-brand {
    position: absolute; left: 0; right: 0; top: 150px;
    display: flex; align-items: center; justify-content: center; gap: 16px;
  }
  .front-brand .brand-dot {
    width: 26px; height: 26px; border-radius: 50%; background: var(--emboss-grey);
  }
  .front-brand .brand-name {
    font-family: "Exo 2", sans-serif; font-weight: 700; font-style: normal;
    font-size: 50px; letter-spacing: 2px; color: var(--emboss-grey);
    text-transform: uppercase;
  }
  .tagline {
    font-family: "Oswald", sans-serif; font-weight: 500;
    color: var(--tag-purple); text-transform: uppercase; letter-spacing: 1px;
    white-space: nowrap;
  }
  .card-front .tagline {
    position: absolute; left: 0; right: 0; top: 333px;
    text-align: center; font-size: 13px;
  }

  /* Back side */
  .card-back { left: 276px; top: 608px; width: 618px; }
  .back-shape { position: absolute; inset: 0; }
  .contact {
    position: absolute; left: 42px; top: 88px; color: var(--white);
    font-family: "Roboto", sans-serif;
  }
  .contact .person-name {
    font-family: "Exo 2", sans-serif; font-weight: 700; font-style: italic;
    font-size: 23px; letter-spacing: 1.5px; text-transform: uppercase;
    line-height: 1;
  }
  .contact .person-role { font-size: 16px; margin-top: 8px; }
  .contact-list { list-style: none; margin-top: 25px; }
  .contact-list li {
    display: flex; align-items: center; font-size: 16px; height: 24px;
  }
  .contact-list svg { width: 13px; height: 13px; margin: 0 15px 0 2px; fill: var(--white); }
  .address { font-size: 16px; line-height: 24px; margin-top: 7px; }

  .back-brand {
    position: absolute; left: 360px; width: 258px; top: 160px;
    display: flex; flex-direction: column; align-items: center;
  }
  .back-brand .brand-row { display: flex; align-items: center; gap: 10px; }
  .back-brand .brand-dot { width: 16px; height: 16px; border-radius: 50%; background: var(--purple-light); }
  .back-brand .brand-name {
    font-family: "Exo 2", sans-serif; font-weight: 700; font-size: 30px;
    letter-spacing: 1.5px; color: var(--white); text-transform: uppercase; line-height: 1;
  }
  .back-brand .tagline { font-size: 9.5px; margin-top: 12px; }
</style>
</head>
<body>

  <section class="card card-front" aria-label="Card front">
    <div class="front-brand">
      <span class="brand-dot"></span>
      <span class="brand-name">Pulse &amp; Pace</span>
    </div>
    <p class="tagline">Personal training.&nbsp; Nutrition. Motivation</p>
  </section>

  <section class="card card-back" aria-label="Card back">
    <svg class="back-shape" viewBox="0 0 618 374" preserveAspectRatio="none" aria-hidden="true">
      <defs>
        <linearGradient id="panelGradient" x1="0" y1="1" x2="1" y2="0">
          <stop offset="0" stop-color="var(--purple-deep)"/>
          <stop offset="0.6" stop-color="var(--purple-mid)"/>
          <stop offset="1" stop-color="var(--purple-light)"/>
        </linearGradient>
      </defs>
      <rect width="618" height="374" fill="url(#panelGradient)"/>
      <path d="M382 0 Q 270 187 388 374 L 618 374 L 618 0 Z" fill="var(--edge-purple)" opacity="0.55"/>
      <path d="M388 0 Q 280 187 392 374 L 618 374 L 618 0 Z" fill="var(--card-black)"/>
    </svg>

    <div class="contact">
      <h1 class="person-name">Marcus Reed</h1>
      <p class="person-role">Personal Trainer</p>
      <ul class="contact-list">
        <li>
          <svg viewBox="0 0 16 16" aria-hidden="true"><path d="M3 1h3l1.5 4-2 1.3a9 9 0 0 0 4.2 4.2L11 8.5l4 1.5v3a2 2 0 0 1-2 2A12 12 0 0 1 1 3a2 2 0 0 1 2-2z"/></svg>
          +1 (555) 204-7731
        </li>
        <li>
          <svg viewBox="0 0 16 16" aria-hidden="true"><path d="M1 3h14v10H1z M2.5 4.5 8 9l5.5-4.5v-.2H2.5z" fill-rule="evenodd"/></svg>
          marcus@pulsepace.com
        </li>
        <li>
          <svg viewBox="0 0 16 16" aria-hidden="true"><path d="M8 1a7 7 0 1 0 0 14A7 7 0 0 0 8 1zm0 1.5c.9 0 1.9 1.8 2.1 4.6H5.9C6.1 4.3 7.1 2.5 8 2.5zM2.6 7.1h1.8c.1-1.5.4-2.8.9-3.7a5.6 5.6 0 0 0-2.7 3.7zm8.9 0h1.9a5.6 5.6 0 0 0-2.8-3.7c.5.9.8 2.2.9 3.7zM2.6 8.9a5.6 5.6 0 0 0 2.7 3.7c-.5-.9-.8-2.2-.9-3.7zm3.3 0c.2 2.8 1.2 4.6 2.1 4.6s1.9-1.8 2.1-4.6zm5.6 0c-.1 1.5-.4 2.8-.9 3.7a5.6 5.6 0 0 0 2.8-3.7z"/></svg>
          www.pulsepace.com
        </li>
      </ul>
      <p class="address">1820 Maple Creek Lane<br>Austin Texas 78701</p>
    </div>

    <div class="back-brand">
      <div class="brand-row">
        <span class="brand-dot"></span>
        <span class="brand-name">Pulse &amp; Pace</span>
      </div>
      <p class="tagline">Personal training.&nbsp; Nutrition. Motivation</p>
    </div>
  </section>

</body>
</html>
```